Automotive Accessories Business Card

Design a business template that match our new logo design and our industry.

https://www.qelmotorgear.com/

Target Market(s)

Aftermarket auto parts and accessories

Industry/Entity Type

automotive

Contact Information for Business Card

company logo

Font styles to use
Serif
Sans Serif

Colors
EB3D1F
EC4F4E
F09395
F8D3D4
FCEDEE

```html
<!DOCTYPE html>
<html lang="en">
<head>
<meta charset="utf-8">
<title>QEL Motor Gear – Business Card</title>
<link rel="stylesheet" href="https://fonts.googleapis.com/css2?family=Montserrat:wght@400;500;700&family=Russo+One&display=swap">
<style>
  :root {
    --red: #db2129;
    --red-light: #e6353b;
    --red-deep: #cf1c24;
    --charcoal: #3b3b3d;
    --white: #ffffff;
    --page: #e3e3e1;
  }
  * { box-sizing: border-box; margin: 0; padding: 0; }
  html, body {
    width: 1200px; height: 800px; overflow: hidden;
    background: var(--page);
    font-family: "Montserrat", Arial, sans-serif;
  }
  .sheet {
    position: relative; width: 1200px; height: 800px;
    display: flex; align-items: center; justify-content: center; gap: 40px;
  }
  .card {
    position: relative; width: 540px; height: 309px; overflow: hidden;
    box-shadow: 0 8px 24px rgba(0,0,0,.18);
  }
  /* Personal side */
  .card--personal { background: var(--white); }
  .card__split { position: absolute; inset: 0; width: 100%; height: 100%; }
  .brand {
    position: absolute; left: 38px; top: 62px;
    display: flex; align-items: center; gap: 10px;
    color: var(--red); font-weight: 700; font-size: 24px; letter-spacing: .5px;
  }
  .brand__square { width: 14px; height: 14px; background: var(--charcoal); }
  .brand__sub {
    position: absolute; left: 62px; top: 96px;
    color: var(--red); font-weight: 700; font-size: 11px; letter-spacing: 2px;
  }
  .person { position: absolute; left: 38px; top: 176px; }
  .person__name {
    font-family: "Russo One", Arial, sans-serif;
    color: var(--red); font-size: 30px; letter-spacing: 1px; line-height: 1;
  }
  .person__title {
    margin-top: 8px; color: var(--charcoal); font-size: 17px; font-weight: 400;
  }
  .contact {
    position: absolute; right: 20px; top: 142px;
    color: var(--white); font-size: 12px; font-weight: 400;
    text-align: right; line-height: 1.5; list-style: none;
  }
  .contact__item { display: flex; justify-content: flex-end; align-items: flex-start; gap: 8px; }
  .contact__item + .contact__item { margin-top: 3px; }
  .contact__icon { width: 11px; height: 11px; flex: none; margin-top: 4px; }
  /* Company side */
  .card--company {
    background: radial-gradient(ellipse at 60% 35%, var(--red-light) 0%, var(--red) 55%, var(--red-deep) 100%);
    color: var(--white);
  }
  .company {
    position: absolute; left: 0; right: 0; top: 78px; text-align: center;
    font-weight: 700;
  }
  .company__name { display: inline-flex; align-items: center; gap: 14px; font-size: 62px; letter-spacing: 4px; line-height: 1; }
  .company__square { width: 22px; height: 22px; background: var(--white); }
  .company__sub { margin-top: 10px; font-size: 17px; letter-spacing: 4px; }
  .products {
    position: absolute; left: 0; right: 0; bottom: 40px; text-align: center;
    font-size: 14px; font-weight: 500; line-height: 1.55;
  }
</style>
</head>
<body>
<main class="sheet">
  <section class="card card--personal" aria-label="Business card, personal side">
    <svg class="card__split" viewBox="0 0 540 309" aria-hidden="true">
      <polygon points="463,0 540,0 540,309 173,309" fill="var(--red)"/>
      <polygon points="444,0 452,0 162,309 154,309" fill="var(--charcoal)"/>
      <polygon points="0,150 14,162 0,174" fill="var(--charcoal)"/>
    </svg>
    <div class="brand"><span class="brand__square"></span>QEL MOTOR GEAR</div>
    <div class="brand__sub">INC</div>
    <div class="person">
      <p class="person__name">DANA REYES</p>
      <p class="person__title">Founder &amp; CEO</p>
    </div>
    <ul class="contact">
      <li class="contact__item">
        <span>240 W. Harbor Ave. Unit B<br>Fresno, CA, 93721<br>United States</span>
        <svg class="contact__icon" viewBox="0 0 12 12" aria-hidden="true"><path d="M6 0a4 4 0 0 0-4 4c0 3 4 8 4 8s4-5 4-8a4 4 0 0 0-4-4zm0 5.5a1.5 1.5 0 1 1 0-3 1.5 1.5 0 0 1 0 3z" fill="#fff"/></svg>
      </li>
      <li class="contact__item">
        <span>1-800-555-0142</span>
        <svg class="contact__icon" viewBox="0 0 12 12" aria-hidden="true"><path d="M2.5 0.5l2 2.5-1.2 1.5c.8 1.7 2.2 3.1 3.9 3.9L8.7 7.2l2.8 2-1 2.3C5.5 11.5.5 6.5.5 1.5z" fill="#fff"/></svg>
      </li>
      <li class="contact__item">
        <span>sales@qelmotorgear.com</span>
        <svg class="contact__icon" viewBox="0 0 12 12" aria-hidden="true"><rect x="0.5" y="2" width="11" height="8" fill="#fff"/><path d="M0.5 2l5.5 4.5L11.5 2" fill="none" stroke="var(--red)" stroke-width="1"/></svg>
      </li>
      <li class="contact__item">
        <span>qelmotorgear.com</span>
        <svg class="contact__icon" viewBox="0 0 12 12" aria-hidden="true"><circle cx="6" cy="6" r="5.5" fill="#fff"/><path d="M0.5 6h11M6 .5c-2.5 3-2.5 8 0 11M6 .5c2.5 3 2.5 8 0 11" fill="none" stroke="var(--red)" stroke-width=".8"/></svg>
      </li>
    </ul>
  </section>

  <section class="card card--company" aria-label="Business card, company side">
    <div class="company">
      <div class="company__name"><span class="company__square"></span>QEL</div>
      <p class="company__sub">MOTOR GEAR INC</p>
    </div>
    <p class="products">
      Nerf Bars | Side Armor | Hitch | Truck Armor | Off-Road<br>
      Grilles | Running Boards | Fender Flare | Fender Trim
    </p>
  </section>
</main>
</body>
</html>
```